Animal Puzzle game Needs Design

Need a redesign of the UI of this puzzle game and a forest background. This game is for any age. The design needs to be on separate layers in Photoshop. The design needs to be colorful and easy to see the different UI parts, sound control, progress bar, number of lives and number of moves.

Target Market(s)

All ages

Requirements
Must have
• Needs to have each of the UI elements and a background.

```html
<!DOCTYPE html>
<html lang="en">
<head>
<meta charset="utf-8">
<title>Forest Puzzle – Game Screen</title>
<link href="https://fonts.googleapis.com/css2?family=Chewy&display=swap" rel="stylesheet">
<style>
  :root {
    --forest-top: #5f8a3a;
    --forest-mid: #8fae4a;
    --forest-light: #c9d77a;
    --meadow: #3f8a3c;
    --meadow-dark: #2f6a2e;
    --bluebell: #7c86c9;
    --wood: #d9b56a;
    --wood-light: #e8cc8a;
    --wood-dark: #5a3a1c;
    --ink: #3b2410;
    --frame: #4a2c14;
    --tile: rgba(225, 238, 250, 0.55);
    --tile-line: #6b6a2a;
    --bar-fill: #8fb4d8;
  }
  * { box-sizing: border-box; margin: 0; padding: 0; }
  html, body { width: 1200px; height: 1042px; overflow: hidden; }
  body { font-family: "Chewy", cursive; color: var(--ink); }

  .game-screen { position: relative; width: 1200px; height: 1042px; overflow: hidden; }

  .forest-backdrop {
    position: absolute; inset: 0;
    background:
      linear-gradient(180deg, rgba(0,0,0,0) 55%, var(--bluebell) 60%, var(--meadow) 68%, var(--meadow-dark) 100%),
      radial-gradient(ellipse at 50% 30%, var(--forest-light) 0%, var(--forest-mid) 40%, var(--forest-top) 80%);
  }

  .plank {
    position: absolute; display: flex; align-items: center; justify-content: center;
    background: linear-gradient(180deg, var(--wood-light), var(--wood));
    border: 2px solid var(--wood-dark); border-radius: 6px;
    box-shadow: 2px 4px 0 rgba(60,35,10,0.45);
    font-size: 30px; letter-spacing: 1px;
  }
  .plank-lives { left: 51px; top: 41px; width: 145px; height: 46px; }
  .plank-level { left: 526px; top: 41px; width: 147px; height: 46px; }
  .plank-moves { left: 1007px; top: 41px; width: 146px; height: 46px; }
  .plank-progress { left: 456px; top: 850px; width: 286px; height: 50px; }

  .stat-badge { position: absolute; }
  .stat-badge text { font-family: "Chewy", cursive; fill: var(--ink); }
  .badge-lives { left: 80px; top: 105px; }
  .badge-level { left: 557px; top: 102px; }
  .badge-moves { left: 1033px; top: 100px; }

  .puzzle-board {
    position: absolute; left: 207px; top: 245px; width: 785px; height: 582px;
    border: 6px solid var(--frame); border-radius: 8px;
    display: grid; grid-template-columns: repeat(7, 1fr); grid-template-rows: repeat(6, 1fr);
    background: linear-gradient(180deg, rgba(230,240,250,0.35), rgba(200,225,245,0.5));
    box-shadow: 0 4px 10px rgba(0,0,0,0.35);
  }
  .puzzle-tile { background: var(--tile); border: 1px solid var(--tile-line); }

  .progress-track {
    position: absolute; left: 210px; top: 913px; width: 777px; height: 66px;
    background: linear-gradient(180deg, var(--wood-light), var(--wood));
    border: 3px solid var(--wood-dark); border-radius: 14px;
    box-shadow: 2px 4px 0 rgba(60,35,10,0.45);
  }
  .progress-fill {
    position: absolute; left: 12px; top: 12px; width: 126px; height: 36px;
    background: linear-gradient(180deg, #c9ddf0, var(--bar-fill) 60%, #6f96bd);
    border: 2px solid #4d6f90; border-radius: 18px;
  }
  .progress-count {
    position: absolute; left: 0; right: 0; top: 14px; text-align: center; font-size: 28px;
  }
  .sound-toggle { position: absolute; left: 1021px; top: 903px; }
</style>
</head>
<body>
<main class="game-screen">
  <div class="forest-backdrop" role="img" aria-label="Illustrated forest with tall tree trunks, green foliage and a meadow of bluebells"></div>

  <div class="plank plank-lives">LIVES</div>
  <svg class="stat-badge badge-lives" width="88" height="82" viewBox="0 0 88 82" aria-label="3 lives">
    <path d="M44 78 C10 54 2 38 4 24 C6 10 18 3 29 4 C37 5 42 10 44 16 C46 10 51 5 59 4 C70 3 82 10 84 24 C86 38 78 54 44 78 Z" fill="#e2c07a" stroke="#5a3a1c" stroke-width="3"/>
    <text x="44" y="46" text-anchor="middle" font-size="26">3</text>
  </svg>

  <div class="plank plank-level">LEVEL</div>
  <svg class="stat-badge badge-level" width="86" height="86" viewBox="0 0 86 86" aria-label="Level 2">
    <circle cx="43" cy="43" r="40" fill="#e2c07a" stroke="#5a3a1c" stroke-width="3"/>
    <text x="43" y="56" text-anchor="middle" font-size="38">2</text>
  </svg>

  <div class="plank plank-moves">MOVES</div>
  <svg class="stat-badge badge-moves" width="92" height="88" viewBox="0 0 92 88" aria-label="10 moves">
    <path d="M46 4 L57 32 L88 33 L63 52 L72 84 L46 66 L20 84 L29 52 L4 33 L35 32 Z" fill="#e2c07a" stroke="#5a3a1c" stroke-width="3" stroke-linejoin="round"/>
    <text x="46" y="56" text-anchor="middle" font-size="22">10</text>
  </svg>

  <section class="puzzle-board" aria-label="Puzzle board">
    <div class="puzzle-tile"></div><div class="puzzle-tile"></div><div class="puzzle-tile"></div><div class="puzzle-tile"></div><div class="puzzle-tile"></div><div class="puzzle-tile"></div><div class="puzzle-tile"></div>
    <div class="puzzle-tile"></div><div class="puzzle-tile"></div><div class="puzzle-tile"></div><div class="puzzle-tile"></div><div class="puzzle-tile"></div><div class="puzzle-tile"></div><div class="puzzle-tile"></div>
    <div class="puzzle-tile"></div><div class="puzzle-tile"></div><div class="puzzle-tile"></div><div class="puzzle-tile"></div><div class="puzzle-tile"></div><div class="puzzle-tile"></div><div class="puzzle-tile"></div>
    <div class="puzzle-tile"></div><div class="puzzle-tile"></div><div class="puzzle-tile"></div><div class="puzzle-tile"></div><div class="puzzle-tile"></div><div class="puzzle-tile"></div><div class="puzzle-tile"></div>
    <div class="puzzle-tile"></div><div class="puzzle-tile"></div><div class="puzzle-tile"></div><div class="puzzle-tile"></div><div class="puzzle-tile"></div><div class="puzzle-tile"></div><div class="puzzle-tile"></div>
    <div class="puzzle-tile"></div><div class="puzzle-tile"></div><div class="puzzle-tile"></div><div class="puzzle-tile"></div><div class="puzzle-tile"></div><div class="puzzle-tile"></div><div class="puzzle-tile"></div>
  </section>

  <div class="plank plank-progress">PROGRESS</div>
  <div class="progress-track">
    <div class="progress-fill"></div>
    <div class="progress-count">28/100</div>
  </div>

  <svg class="sound-toggle" width="104" height="86" viewBox="0 0 104 86" aria-label="Sound on">
    <path d="M6 30 H24 L48 8 V78 L24 56 H6 Z" fill="#e2c07a" stroke="#5a3a1c" stroke-width="3" stroke-linejoin="round"/>
    <path d="M60 30 Q68 43 60 56" fill="none" stroke="#e2c07a" stroke-width="7" stroke-linecap="round"/>
    <path d="M72 20 Q86 43 72 66" fill="none" stroke="#e2c07a" stroke-width="7" stroke-linecap="round"/>
    <path d="M84 10 Q104 43 84 76" fill="none" stroke="#e2c07a" stroke-width="7" stroke-linecap="round"/>
  </svg>
</main>
</body>
</html>
```